Dynamic Business Card for Sports Supplements Company

Hi! I'm looking for an awesome business card to match my existing sports supplement company. I have uploaded my current company logo and screenshot of the front page of my website.

I would like to have something dynamic and interesting and utilize the colors in the website - the reds and purples

The business card should be double sided and focus on a unique eye-catching design on the back and include all the relevant company info.

Most importantly, it should say somewhere: "Sign up on our website for a coupon code."

Target Market(s)

Mostly for women gym goers but it shouldn't be too feminine. It should be in keeping with the website design. It should flow and clearly be connected to it

Industry/Entity Type

Business

Contact Information for Business Card

Lorraine K. Vestal
CEO
LVestal@Quorvanexco.com
www.quorvanexco.com
555.417.3820
P.O. Box 47315
Larkdale, Norvale 00000

Sign up on our website for a coupon code

Font styles to use
Serif
Sans Serif
Other font styles liked:
• Novecento font family and "Quorvanex" is in AR Destine font

Requirements
Must have
• One side should be a bold Quorvanex logo design. Even just the symbol itself may be o.k. (see attached file)

```html
<!DOCTYPE html>
<html lang="en">
<head>
<meta charset="utf-8">
<title>Quorvanex Business Card</title>
<link rel="stylesheet" href="https://fonts.googleapis.com/css2?family=Open+Sans:wght@400;600;700&display=swap">
<style>
  :root {
    --page-bg: #2b2b2d;
    --card-bg: #1f2023;
    --card-edge: #2a2b2f;
    --ink: #ffffff;
    --accent: #e3222a;
    --muted: #d9d9d9;
  }
  * { box-sizing: border-box; margin: 0; padding: 0; }
  html, body { width: 1200px; height: 1189px; overflow: hidden; }
  body {
    background: var(--page-bg);
    font-family: "Open Sans", Arial, sans-serif;
    color: var(--ink);
    position: relative;
  }
  .card {
    position: absolute;
    left: 150px;
    width: 900px;
    height: 514px;
    border-radius: 34px;
    background: linear-gradient(135deg, var(--card-edge), var(--card-bg) 60%);
    box-shadow: 0 18px 40px rgba(0,0,0,0.45);
    overflow: hidden;
  }
  .card--back { top: 48px; }
  .card--front { top: 626px; }

  /* back side */
  .back-brand {
    position: absolute;
    left: 0; right: 0; top: 150px;
    text-align: center;
  }
  .brand-name {
    font-weight: 700;
    color: var(--ink);
    letter-spacing: 2px;
    text-transform: uppercase;
    display: inline-flex;
    align-items: center;
    gap: 18px;
  }
  .brand-mark {
    display: inline-block;
    background: var(--accent);
  }
  .back-brand .brand-name { font-size: 66px; }
  .back-brand .brand-mark { width: 46px; height: 46px; }
  .tagline {
    text-transform: uppercase;
    color: var(--ink);
    margin-top: 6px;
  }
  .back-brand .tagline { font-size: 17px; letter-spacing: 6px; }
  .signup {
    position: absolute;
    left: 0; right: 0; top: 336px;
    text-align: center;
    font-size: 30px;
    color: var(--ink);
  }
  .signup__lead { color: var(--accent); }

  /* front side */
  .front-brand {
    position: absolute;
    left: 70px; top: 110px;
  }
  .front-brand .brand-name { font-size: 54px; gap: 14px; }
  .front-brand .brand-mark { width: 38px; height: 38px; }
  .front-brand .tagline { font-size: 14px; letter-spacing: 5px; }

  .holder {
    position: absolute;
    right: 70px; top: 168px;
    text-align: right;
  }
  .holder__name { font-size: 33px; font-weight: 700; letter-spacing: 0.5px; }
  .divider {
    position: absolute;
    left: 70px; right: 70px; top: 236px;
    height: 2px;
    background: var(--accent);
  }
  .holder__title {
    position: absolute;
    right: 70px; top: 240px;
    font-size: 24px;
    color: var(--accent);
  }

  .contact-list {
    position: absolute;
    left: 70px; top: 318px;
    list-style: none;
  }
  .contact-list li {
    display: flex;
    align-items: center;
    gap: 16px;
    font-size: 28px;
    line-height: 1;
    height: 42px;
  }
  .contact-icon {
    width: 28px; height: 28px;
    border-radius: 5px;
    background: var(--accent);
    display: inline-flex;
    align-items: center;
    justify-content: center;
    flex-shrink: 0;
  }
  .address {
    position: absolute;
    right: 70px; top: 326px;
    text-align: right;
    font-size: 28px;
    line-height: 1.4;
    font-style: normal;
    color: var(--muted);
  }
</style>
</head>
<body>

<section class="card card--back" aria-label="Card back">
  <div class="back-brand">
    <div class="brand-name"><span class="brand-mark"></span>Quorvanex</div>
    <div class="tagline">Your Training Companion</div>
  </div>
  <p class="signup"><span class="signup__lead">Sign up</span> on our website for a coupon code</p>
</section>

<section class="card card--front" aria-label="Card front">
  <div class="front-brand">
    <div class="brand-name"><span class="brand-mark"></span>Quorvanex</div>
    <div class="tagline">Your Training Companion</div>
  </div>

  <div class="holder">
    <div class="holder__name">Lorraine K. Vestal</div>
  </div>
  <div class="divider"></div>
  <div class="holder__title">CEO</div>

  <ul class="contact-list">
    <li>
      <span class="contact-icon">
        <svg width="18" height="18" viewBox="0 0 24 24" aria-hidden="true"><path fill="#fff" d="M6.6 10.8a15.1 15.1 0 0 0 6.6 6.6l2.2-2.2c.3-.3.7-.4 1-.2 1.1.4 2.3.6 3.6.6.6 0 1 .4 1 1V20c0 .6-.4 1-1 1A17 17 0 0 1 3 4c0-.6.4-1 1-1h3.5c.6 0 1 .4 1 1 0 1.3.2 2.5.6 3.6.1.3 0 .7-.2 1z"/></svg>
      </span>555.417.3820
    </li>
    <li>
      <span class="contact-icon">
        <svg width="18" height="18" viewBox="0 0 24 24" aria-hidden="true"><rect x="3" y="6" width="18" height="12" fill="none" stroke="#fff" stroke-width="2"/><path d="M3 6l9 7 9-7" fill="none" stroke="#fff" stroke-width="2"/></svg>
      </span>LVestal@Quorvanexco.com
    </li>
    <li>
      <span class="contact-icon">
        <svg width="18" height="18" viewBox="0 0 24 24" aria-hidden="true"><g fill="none" stroke="#fff" stroke-width="1.8"><circle cx="12" cy="12" r="9"/><ellipse cx="12" cy="12" rx="4" ry="9"/><path d="M3 12h18M5 7h14M5 17h14"/></g></svg>
      </span>www.quorvanexco.com
    </li>
  </ul>

  <address class="address">
    P.O. Box 47315<br>
    Larkdale, Norvale 00000
  </address>
</section>

</body>
</html>
```